ORLA - Óptica Médica - web design and concept

Website concept - Create and develop our website design and structure. ORLA is an optical store chain, and we are looking to establish our web and digital concept. In attachment there are several pictures about our stores and our logo.

The website structure should be user friendly. Colors should be light and the design as simple and minimalist as possible. There are different variations of the logothat can be used, check the file.

The website will include optical collections and sun collections as an online store. Also, a medical menu should be considered in order for clients to schedule optometry appointments. There should also be a menu for client assistance where the clients can read about glass maintenance in our workshop.
Updates

Low design quality

Number of Pages Required

5+ page

Font styles to use
Serif
Sans Serif

Requirements
Must have
• Must be user-friendly and minimalist.
• Please USE PICTURES FROM THE BRANDS we sell: MERUN, BOSKA, PNW, KOLE, BAMPE
Nice to have
• Nice to inspire: ZEK glasses (see website https://ch.shopzek.com/en/)
• Nice to inspire: https://merun-eyewear.com/
• Nice to ispire: https://www.pnwglobe.com/en/
Should not have
• Hysteric colors and shapes

```html
<!DOCTYPE html>
<html lang="en">
<head>
<meta charset="utf-8">
<title>ORLA Optica Medica</title>
<link href="https://fonts.googleapis.com/css2?family=Raleway:wght@400;500;600;700&family=Open+Sans:wght@400;600;700&display=swap" rel="stylesheet">
<style>
:root{
  --gold:#d39a45;
  --ink:#111;
  --black:#0b0b0b;
  --text:#555;
  --panel:#f2f2f2;
  --line:#cfcfcf;
  --white:#fff;
}
*{box-sizing:border-box;margin:0;padding:0}
html,body{width:1200px;height:3125px;overflow:hidden}
body{position:relative;background:var(--white);font-family:"Open Sans",sans-serif;color:var(--text)}
.abs{position:absolute}

/* header */
.site-header{left:0;top:0;width:1200px;height:88px;background:var(--black);z-index:3}
.brand-mark{left:60px;top:0;width:220px;height:198px;background:var(--black);z-index:4;
  clip-path:polygon(0 0,100% 0,100% 60%,50% 100%,0 60%);display:flex;align-items:flex-start;justify-content:center;padding-top:60px}
.brand-name{font-family:"Raleway",sans-serif;font-weight:500;font-size:40px;letter-spacing:6px;color:var(--gold)}
.main-nav{right:200px;top:0;height:88px;display:flex;align-items:center;gap:40px;z-index:4}
.main-nav a{font-family:"Raleway",sans-serif;font-size:15px;font-weight:500;color:var(--white);text-decoration:none;letter-spacing:.3px}
.main-nav a.active{color:var(--gold)}
.header-tools{right:72px;top:20px;display:flex;gap:14px;z-index:4}
.tool{width:46px;height:46px;border-radius:50%;display:flex;align-items:center;justify-content:center}
.tool.search{border:2px solid var(--white)}
.tool.cart{background:var(--gold)}

/* hero */
.hero{left:0;top:88px;width:1200px;height:506px;background:linear-gradient(180deg,#3b352c 0%,#5e5546 45%,#8c7c62 75%,#b8a789 100%)}
.hero-shade{inset:0;background:radial-gradient(ellipse at 50% 45%,rgba(58,118,120,.35),rgba(0,0,0,.35))}
.hero-title{left:0;top:188px;width:1200px;text-align:center;font-family:"Raleway",sans-serif;font-weight:700;font-size:76px;color:var(--white);letter-spacing:1px}
.hero-lead{left:270px;top:282px;width:660px;text-align:center;font-size:20px;line-height:32px;color:var(--white)}
.btn{display:flex;align-items:center;justify-content:center;border-radius:30px;font-family:"Open Sans",sans-serif;font-weight:700;text-transform:uppercase}
.hero-btn{left:479px;top:375px;width:242px;height:52px;background:var(--gold);color:var(--white);font-size:15px}
.hero-dots{left:564px;top:530px;display:flex;gap:6px}
.hero-dots span{width:13px;height:13px;border-radius:50%;border:2px solid var(--white)}
.hero-dots span.on{background:var(--white)}

/* welcome */
.section-title{font-family:"Raleway",sans-serif;font-weight:500;color:var(--ink);text-align:center;width:1200px;left:0}
.welcome-title{top:672px;font-size:40px}
.welcome-text{left:225px;top:744px;width:750px;text-align:center;font-size:13px;line-height:26px}
.video{left:396px;top:840px;width:406px;height:260px;background:#fff;padding:6px;box-shadow:0 6px 22px rgba(0,0,0,.35)}
.video-still{width:100%;height:100%;background:linear-gradient(180deg,#2b2721 0%,#6a604f 45%,#cfc9c0 70%,#ece8e2 100%);position:relative}
.play{position:absolute;left:174px;top:100px;width:52px;height:52px;border-radius:50%;background:#111;display:flex;align-items:center;justify-content:center}

/* products */
.band{left:0;top:1188px;width:1200px;height:81px;background:var(--gold);display:flex;align-items:center;justify-content:center;
  font-family:"Raleway",sans-serif;font-size:38px;font-weight:500;color:var(--white)}
.product-card{top:1333px;width:240px;height:238px;border:1px solid var(--line);background:#fff}
.product-photo{height:186px}
.product-label{height:50px;display:flex;align-items:center;justify-content:center;font-family:"Raleway",sans-serif;font-weight:500;font-size:18px;color:var(--ink);border-top:1px solid var(--line)}
.carousel-arrow{top:1405px;width:46px;height:46px;border-radius:50%;border:1px solid #333;display:flex;align-items:center;justify-content:center;background:#fff}

/* what we do */
.about-photo{left:0;top:1679px;width:600px;height:509px;background:linear-gradient(90deg,#1a1a1a 0%,#3c7f85 30%,#8d7350 50%,#3c7f85 70%,#1a1a1a 100%)}
.about-panel{left:600px;top:1679px;width:600px;height:509px;background:var(--panel)}
.about-title{left:652px;top:1718px;font-family:"Raleway",sans-serif;font-weight:500;font-size:40px;color:var(--ink)}
.about-text{left:652px;top:1782px;width:460px;font-size:13px;line-height:27.5px}
.about-text p+p{margin-top:26px}
.read-more{left:652px;top:2088px;width:140px;height:47px;border:2px solid var(--gold);color:var(--gold);font-size:14px;background:transparent}

/* features */
.features{left:0;top:2188px;width:1200px;height:179px;display:flex;border-top:1px solid var(--line);border-bottom:1px solid var(--line)}
.feature{flex:1;border-right:1px solid var(--line);display:flex;flex-direction:column;align-items:center;padding-top:30px}
.feature:last-child{border-right:0}
.feature svg{height:56px}
.feature-name{margin-top:10px;text-align:center;font-family:"Open Sans",sans-serif;font-size:19px;line-height:25px;color:var(--ink)}

/* brands */
.brands-title{top:2455px;font-size:40px}
.brand-box{top:2550px;width:187px;height:96px;border:1px solid #bbb;display:flex;align-items:center;justify-content:center;
  font-family:"Raleway",sans-serif;font-weight:600;font-size:20px;color:#666;letter-spacing:1px}

/* footer */
.site-footer{left:0;top:2750px;width:1200px;height:375px;background:var(--black);color:var(--white)}
.foot-col{top:68px}
.foot-col h4{font-family:"Open Sans",sans-serif;font-weight:700;font-size:14.5px;letter-spacing:.3px;margin-bottom:14px}
.foot-col li{list-style:none;font-size:12px;line-height:27.5px;color:#e6e6e6}
.subscribe-lead{font-size:12px;margin-bottom:18px;color:#e6e6e6}
.subscribe{display:flex;width:324px;height:35px}
.subscribe .field{flex:1;background:var(--black);border:1px solid #fff;font-size:11px;color:#ddd;padding-left:12px;display:flex;align-items:center}
.subscribe .go{width:92px;background:var(--gold);font-size:11px;font-weight:700;display:flex;align-items:center;justify-content:center}
.stay{margin-top:14px}
.socials{display:flex;gap:9px}
.socials span{width:34px;height:34px;border-radius:50%;border:2px solid #fff}
.copyright{left:0;top:318px;width:1200px;text-align:center;font-size:11.5px;color:#ddd}
</style>
</head>
<body>

<header class="abs site-header"></header>
<div class="abs brand-mark"><span class="brand-name">ORLA</span></div>
<nav class="abs main-nav">
  <a class="active" href="#">START</a><a href="#">ABOUT US</a><a href="#">PRODUCTS</a><a href="#">CONTACT</a><a href="#">BLOG</a><a href="#">STORE</a>
</nav>
<div class="abs header-tools">
  <span class="tool search"><svg width="18" height="18" viewBox="0 0 18 18"><circle cx="7.5" cy="7.5" r="5.5" fill="none" stroke="#fff" stroke-width="2.5"/><line x1="11.5" y1="11.5" x2="16" y2="16" stroke="#fff" stroke-width="2.5" stroke-linecap="round"/></svg></span>
  <span class="tool cart"><svg width="20" height="18" viewBox="0 0 20 18"><path d="M1 2h3l2.5 9h9l2.5-7H5.5" fill="#fff" stroke="#fff" stroke-width="1.5"/><circle cx="8" cy="15" r="1.8" fill="#fff"/><circle cx="14" cy="15" r="1.8" fill="#fff"/></svg></span>
</div>

<section class="abs hero" role="img" aria-label="Interior of an ORLA optical store with teal wall panels and round display mirrors">
  <div class="abs hero-shade"></div>
</section>
<h1 class="abs hero-title">ORLA OPTICA</h1>
<p class="abs hero-lead">We are an optical store chain. We are focused on bringing the best optical assistance and eyewear brands to our costumers.</p>
<a class="abs btn hero-btn">Get to know us better!</a>
<div class="abs hero-dots"><span class="on"></span><span></span><span></span><span></span></div>

<h2 class="abs section-title welcome-title">WELCOME TO ORLA OPTICA</h2>
<p class="abs welcome-text">ORLA OPTICA opens its doors with a clear purpose: to take care of you. Our priority is your visual health, and for this reason we have the best professionals and the most competitive products to serve your needs.</p>
<div class="abs video"><div class="video-still" role="img" aria-label="Video still of the store interior with a central wooden display table">
  <span class="play"><svg width="20" height="22" viewBox="0 0 20 22"><path d="M3 1l16 10L3 21z" fill="#fff"/></svg></span>
</div></div>

<div class="abs band">OUR PRODUCTS</div>
<span class="abs carousel-arrow" style="left:25px"><svg width="12" height="16" viewBox="0 0 12 16"><path d="M9 2L3 8l6 6" fill="none" stroke="#333" stroke-width="2"/></svg></span>
<span class="abs carousel-arrow" style="left:1127px"><svg width="12" height="16" viewBox="0 0 12 16"><path d="M3 2l6 6-6 6" fill="none" stroke="#333" stroke-width="2"/></svg></span>
<div class="abs product-card" style="left:98px"><div class="product-photo" role="img" aria-label="Woman wearing black prescription frames" style="background:linear-gradient(135deg,#d9d9d9,#6b5a50)"></div><div class="product-label">GRADUATED FRAME</div></div>
<div class="abs product-card" style="left:352px"><div class="product-photo" role="img" aria-label="Two clear ophthalmic lenses" style="background:linear-gradient(135deg,#e9e6e2,#bdb8b2)"></div><div class="product-label">OPHTHALMIC LENSES</div></div>
<div class="abs product-card" style="left:606px"><div class="product-photo" role="img" aria-label="Child wearing red glasses" style="background:linear-gradient(135deg,#dfe8ea,#c9a083)"></div><div class="product-label">SPECIAL CHILDREN</div></div>
<div class="abs product-card" style="left:862px"><div class="product-photo" role="img" aria-label="Couple wearing sunglasses outdoors" style="background:linear-gradient(135deg,#e4a23a,#b56a3e)"></div><div class="product-label">SUN GLASSES</div></div>

<div class="abs about-photo" role="img" aria-label="Store display wall with teal panels and round mirror shelves"></div>
<div class="abs about-panel"></div>
<h2 class="abs about-title">WHAT WE DO</h2>
<div class="abs about-text">
  <p>He specializes in contact lenses. He graduated in Optics and Optometry and holds two master's degrees ( Research in Vision and Low Vision Sciences and Visual Rehabilitation ).</p>
  <p>He has extensive experience in customer service, which has combined with his facet as a researcher. Until 2016 he worked as a specialist and trainer at Lentavis, a prestigious multinational dedicated to the development and adaptation of special contact lenses. Nobody better than Tomás Ibarra to advise you on the latest treatments and developments in the sector.</p>
</div>
<a class="abs btn read-more">Read more</a>

<div class="abs features">
  <div class="feature"><svg viewBox="0 0 40 56" width="40"><circle cx="20" cy="8" r="6" fill="var(--gold)"/><path d="M6 16l8 6h12l8-6 3 4-9 7v27h-6V40h-4v14h-6V27l-9-7z" fill="var(--gold)"/></svg><div class="feature-name">Orla Childhood<br>Guarantee</div></div>
  <div class="feature"><svg viewBox="0 0 70 56" width="70"><path d="M14 10h42l8 18v20H6V28z" fill="var(--gold)"/><path d="M18 16h34l5 12H13z" fill="#fff"/><circle cx="16" cy="36" r="4" fill="#fff"/><circle cx="54" cy="36" r="4" fill="#fff"/><rect x="8" y="46" width="12" height="8" fill="var(--gold)"/><rect x="50" y="46" width="12" height="8" fill="var(--gold)"/></svg><div class="feature-name">Orla Accident<br>Warranty</div></div>
  <div class="feature"><svg viewBox="0 0 44 56" width="44"><path d="M2 4h40v22c0 14-10 24-20 28C12 50 2 40 2 26z" fill="var(--gold)"/><path d="M22 10h14v16c0 10-7 18-14 21z" fill="#fff"/></svg><div class="feature-name">Orla<br>Security</div></div>
  <div class="feature"><svg viewBox="0 0 60 56" width="60"><path d="M2 28C12 14 48 14 58 28 48 42 12 42 2 28z" fill="var(--gold)"/><circle cx="30" cy="28" r="10" fill="#fff"/><circle cx="30" cy="28" r="6" fill="var(--gold)"/></svg><div class="feature-name">Orla<br>Vision</div></div>
  <div class="feature"><svg viewBox="0 0 56 56" width="56"><path d="M28 2l6 8 10-2 1 10 9 5-5 9 5 9-9 5-1 10-10-2-6 8-6-8-10 2-1-10-9-5 5-9-5-9 9-5 1-10 10 2z" fill="var(--gold)"/></svg><div class="feature-name">Manufacturer's<br>Warranty</div></div>
</div>

<h2 class="abs section-title brands-title">OUR BRANDS</h2>
<div class="abs brand-box" style="left:98px">VARDEN</div>
<div class="abs brand-box" style="left:302px">CORSALA</div>
<div class="abs brand-box" style="left:506px">LUMETTI</div>
<div class="abs brand-box" style="left:711px">JANE ORLO</div>
<div class="abs brand-box" style="left:915px">ISADORA VEGA</div>

<footer class="abs site-footer">
  <div class="abs foot-col" style="left:100px"><h4>INFORMATION</h4><ul><li>About Us</li><li>Careers</li><li>Privacy &amp; Security</li><li>Site Map</li><li>Terms of Use</li><li>Blog</li></ul></div>
  <div class="abs foot-col" style="left:302px"><h4>HELP &amp; SUPPORT</h4><ul><li>Recommended Reading</li><li>Submit your Story</li><li>Contact Us</li><li>Frequently Asked Questions</li><li>How to Order</li></ul></div>
  <div class="abs foot-col" style="left:552px"><h4>MY ACCOUNT</h4><ul><li>Delivery Information</li><li>My Account</li><li>Order Tracking</li><li>Reminder Service</li><li>Shipping, Returns &amp; Fees</li></ul></div>
  <div class="abs foot-col" style="left:777px">
    <h4>EMAIL SUBSCRIPTION</h4>
    <p class="subscribe-lead">Register your email address to get information about us</p>
    <div class="subscribe"><span class="field">Email Address</span><span class="go">SUBSCRIBE</span></div>
    <h4 class="stay">STAY CONNECTED</h4>
    <div class="socials"><span></span><span></span><span></span></div>
  </div>
  <p class="abs copyright">Copyrights © 2018, ORLA Optica. All Rights Reserved.</p>
</footer>

</body>
</html>
```